Mindfulness School for Children -- Business Cards

We're looking for business cards for our school directors and owners. We're a mindfulness school for children called little lanterns. Attached are our logos/icons.

```html
<!DOCTYPE html>
<html lang="en">
<head>
<meta charset="utf-8">
<title>little lanterns — business cards</title>
<link rel="stylesheet" href="https://fonts.googleapis.com/css2?family=Lora:wght@400&family=Karla:wght@400&display=swap">
<style>
  :root {
    --backdrop: #4a403b;
    --card: #2a2a2a;
    --teal: #4fb8c8;
    --mint: #6cc5a8;
    --text-light: #c9c9c9;
  }
  * { margin: 0; padding: 0; box-sizing: border-box; }
  html, body { width: 1200px; height: 716px; overflow: hidden; }
  body {
    background: var(--backdrop);
    display: flex;
    align-items: center;
    justify-content: center;
    gap: 40px;
  }
  .card {
    width: 540px;
    height: 309px;
    background: var(--card);
    position: relative;
    box-shadow: 0 10px 28px rgba(0, 0, 0, 0.45);
  }
  .card-back { padding: 58px 0 0 62px; }
  .person-name {
    font-family: "Lora", serif;
    font-size: 30px;
    color: var(--teal);
    line-height: 1.1;
  }
  .person-role {
    font-family: "Karla", sans-serif;
    font-size: 14px;
    color: var(--mint);
    margin: 2px 0 20px 0;
  }
  .contact-list { list-style: none; }
  .contact-item {
    display: flex;
    align-items: flex-start;
    gap: 10px;
    font-family: "Karla", sans-serif;
    font-size: 14px;
    line-height: 1.35;
    color: var(--text-light);
    margin-bottom: 4px;
  }
  .contact-icon { width: 12px; height: 12px; margin-top: 3px; flex: none; }
  .card-front {
    display: flex;
    align-items: center;
    justify-content: flex-end;
    padding-right: 70px;
  }
  .brand {
    display: flex;
    align-items: center;
    gap: 10px;
  }
  .brand-mark {
    width: 14px; height: 14px;
    border-radius: 50%;
    background: var(--teal);
  }
  .brand-name {
    font-family: "Lora", serif;
    font-size: 40px;
    color: var(--teal);
  }
</style>
</head>
<body>
  <section class="card card-back">
    <h1 class="person-name">Daniel Harper</h1>
    <p class="person-role">President</p>
    <ul class="contact-list">
      <li class="contact-item">
        <svg class="contact-icon" viewBox="0 0 12 12"><path d="M6 0.5a4 4 0 0 1 4 4c0 3-4 7-4 7s-4-4-4-7a4 4 0 0 1 4-4z" fill="var(--mint)"/><circle cx="6" cy="4.5" r="1.4" fill="var(--card)"/></svg>
        <span>1420 Willow Creek Road<br>Juneau, Alaska 99801</span>
      </li>
      <li class="contact-item">
        <svg class="contact-icon" viewBox="0 0 12 12"><path d="M2.5 1l2 0 1 3-1.3 1a6 6 0 0 0 2.8 2.8l1-1.3 3 1 0 2c0 .8-.7 1.5-1.5 1.5A9 9 0 0 1 1 2.5C1 1.7 1.7 1 2.5 1z" fill="var(--mint)"/></svg>
        <span>555-014-2278</span>
      </li>
      <li class="contact-item">
        <svg class="contact-icon" viewBox="0 0 12 12"><rect x="0.5" y="2" width="11" height="8" rx="1" fill="var(--mint)"/><path d="M1 2.5l5 4 5-4" stroke="var(--card)" fill="none"/></svg>
        <span>hello@littlelanterns.com</span>
      </li>
      <li class="contact-item">
        <svg class="contact-icon" viewBox="0 0 12 12"><circle cx="6" cy="6" r="5.5" fill="var(--mint)"/><path d="M0.5 6h11M6 0.5c-2.5 3-2.5 8 0 11M6 0.5c2.5 3 2.5 8 0 11" stroke="var(--card)" fill="none" stroke-width="0.8"/></svg>
        <span>littlelanterns.com</span>
      </li>
    </ul>
  </section>

  <section class="card card-front">
    <div class="brand">
      <span class="brand-name">little lanterns</span>
      <span class="brand-mark"></span>
    </div>
  </section>
</body>
</html>
```